Professional BIO Template with photo and logo

Hello,
I need a professional Bio template developed via Microsoft WORD ASAP!!!!! I would like to just be able to add the text I need to add. So resize-able text boxes. Potentially able to adjust the font. These are the things I need added it to include.
Head shot (attached)
Text Box for Name
Text Box for phone number
Text box for email
KVT Logo (attached)
Maybe a blue banner at the top or some background boxes that are blue or grey. Here are the pantone colors that our company uses.

CORE COLOR
100c 91m 17y 6k 38r 58g 128b Hex #263A80 Pantone 7687 C

CORE CONTRAST COLOR
36c 29m 28y 0k 168r 168g 170b Hex #669999 Pantone Cool Gray 6C

I also attached some examples of what we have been looking at. Instead of green add the blue...instead of black maybe just be white.

Thank you

```html
<!DOCTYPE html>
<html lang="en">
<head>
<meta charset="utf-8">
<title>Daniel Harlow – Bio</title>
<link href="https://fonts.googleapis.com/css2?family=Tinos:wght@400;700&family=Roboto:wght@500&display=swap" rel="stylesheet">
<style>
  :root {
    --core-blue: #263a80;
    --header-blue: #223481;
    --header-deep: #16245e;
    --teal: #669999;
    --teal-deep: #3f8585;
    --white: #ffffff;
    --page-bg: #e9ebee;
  }
  html, body {
    margin: 0;
    padding: 0;
    width: 1200px;
    height: 1174px;
    overflow: hidden;
    background: var(--page-bg);
  }
  .bio-sheet {
    position: absolute;
    left: 199px;
    top: 20px;
    width: 802px;
    height: 1134px;
    overflow: hidden;
    background: linear-gradient(180deg, var(--teal) 0%, var(--teal) 70%, var(--teal-deep) 100%);
    font-family: "Tinos", "Times New Roman", serif;
    color: var(--white);
    box-shadow: 0 6px 24px rgba(0,0,0,.18);
  }
  .header-band {
    position: absolute;
    left: 0; top: 0;
    width: 802px; height: 286px;
    background: linear-gradient(180deg, var(--header-blue) 0%, #233a7e 55%, var(--header-deep) 100%);
  }
  .brand-name {
    position: absolute;
    left: 0; top: 34px;
    width: 802px;
    text-align: center;
    font-weight: 700;
    font-size: 40px;
    letter-spacing: 4px;
    line-height: 1;
  }
  .corner-accent {
    position: absolute;
    left: 0; top: 0;
  }
  .portrait-frame {
    position: absolute;
    left: 81px; top: 122px;
    width: 253px; height: 325px;
    border: 1px solid var(--white);
  }
  .portrait {
    position: absolute;
    left: 90px; top: 134px;
    width: 237px; height: 303px;
    background: radial-gradient(ellipse at 50% 35%, #6a6a6c 0%, #3d3d40 60%, #2a2a2d 100%);
  }
  .person-name {
    position: absolute;
    left: 357px; top: 196px;
    margin: 0;
    font-size: 66px;
    font-weight: 700;
    line-height: 1;
    white-space: nowrap;
  }
  .contact-icon {
    position: absolute;
    width: 48px; height: 48px;
    border-radius: 50%;
    background: var(--white);
    box-shadow: 0 3px 6px rgba(0,0,0,.25);
  }
  .contact-icon svg { position: absolute; left: 14px; top: 14px; }
  .contact-label {
    position: absolute;
    left: 428px;
    font-size: 16px;
    font-weight: 700;
    line-height: 1;
  }
  .contact-value {
    position: absolute;
    left: 428px;
    font-size: 23px;
    font-weight: 700;
    line-height: 1;
  }
  .about-frame {
    position: absolute;
    left: 67px; top: 508px;
    width: 663px; height: 581px;
    border: 1px solid var(--white);
  }
  .about-title {
    position: absolute;
    left: 82px; top: 490px;
    width: 177px; height: 51px;
    margin: 0;
    background: var(--core-blue);
    font-size: 32px;
    font-weight: 700;
    line-height: 51px;
    text-align: center;
  }
  .about-text {
    position: absolute;
    left: 81px;
    width: 636px;
    margin: 0;
    font-family: "Roboto", Arial, sans-serif;
    font-weight: 500;
    font-size: 11.2px;
    line-height: 17.8px;
    text-align: justify;
  }
</style>
</head>
<body>
  <main class="bio-sheet">
    <div class="header-band" role="img" aria-label="Night city skyline photograph in deep blue tones"></div>
    <div class="brand-name">KVT</div>

    <svg class="corner-accent" width="802" height="1134" viewBox="0 0 802 1134" aria-hidden="true">
      <polygon points="686,286 802,286 802,402" fill="#263a80"/>
      <polygon points="802,1018 686,1134 802,1134" fill="#263a80"/>
    </svg>

    <div class="portrait-frame"></div>
    <div class="portrait" role="img" aria-label="Head shot portrait of Daniel Harlow"></div>

    <h1 class="person-name">Daniel Harlow</h1>

    <div class="contact-icon" style="left:364px; top:307px;">
      <svg width="20" height="20" viewBox="0 0 24 24" aria-hidden="true">
        <path fill="#263a80" d="M6.6 10.8a15.1 15.1 0 0 0 6.6 6.6l2.2-2.2a1 1 0 0 1 1-.25 11.4 11.4 0 0 0 3.6.57 1 1 0 0 1 1 1V20a1 1 0 0 1-1 1A17 17 0 0 1 3 4a1 1 0 0 1 1-1h3.5a1 1 0 0 1 1 1c0 1.25.2 2.45.57 3.57a1 1 0 0 1-.25 1z"/>
      </svg>
    </div>
    <div class="contact-label" style="top:304px;">Phone :</div>
    <div class="contact-value" style="top:333px;">+1 888 888 8888</div>

    <div class="contact-icon" style="left:364px; top:392px;">
      <svg width="20" height="20" viewBox="0 0 24 24" aria-hidden="true">
        <path fill="#263a80" d="M2 5h20v2.2l-10 6.3L2 7.2z M2 9.6l10 6.3 10-6.3V19H2z"/>
      </svg>
    </div>
    <div class="contact-label" style="top:394px;">Email Address :</div>
    <div class="contact-value" style="top:424px;">info@companyname.com</div>

    <div class="about-frame"></div>
    <h2 class="about-title">About Me</h2>

    <p class="about-text" style="top:561px;">Lorem ipsum dolor sit amet, consectetur adipiscing elit, sed do eiusmod tempor incididunt ut labore et dolore magna aliqua. Ut enim ad minim veniam, quis nostrud exercitation ullamco laboris nisi ut aliquip ex ea commodo consequat. Duis aute irure dolor in reprehenderit in voluptate velit esse cillum dolore eu fugiat nulla pariatur. Excepteur sint occaecat cupidatat non proident, sunt in culpa qui officia deserunt mollit anim id est laborum. Lorem ipsum dolor sit amet, consectetur adipiscing elit, sed do eiusmod tempor incididunt ut labore et dolore magna aliqua. Ut enim ad minim veniam, quis nostrud exercitation ullamco laboris nisi ut aliquip ex ea commodo consequat. Duis aute irure dolor in reprehenderit in voluptate velit esse cillum dolore eu fugiat nulla pariatur.</p>

    <p class="about-text" style="top:703px;">Excepteur sint occaecat cupidatat non proident, sunt in culpa qui officia deserunt mollit anim id est laborum. Lorem ipsum dolor sit amet, consectetur adipiscing elit, sed do eiusmod tempor incididunt ut labore et dolore magna aliqua. Ut enim ad minim veniam, quis nostrud exercitation ullamco laboris nisi ut aliquip ex ea commodo consequat. Duis aute irure dolor in reprehenderit in voluptate velit esse cillum dolore eu fugiat nulla pariatur. Excepteur sint occaecat cupidatat non proident, sunt in culpa qui officia deserunt mollit anim id est laborum. Lorem ipsum dolor sit amet, consectetur adipiscing elit, sed do eiusmod tempor incididunt ut labore et dolore magna aliqua.</p>

    <p class="about-text" style="top:845px;">Ut enim ad minim veniam, quis nostrud exercitation ullamco laboris nisi ut aliquip ex ea commodo consequat. Duis aute irure dolor in reprehenderit in voluptate velit esse cillum dolore eu fugiat nulla pariatur. Excepteur sint occaecat cupidatat non proident, sunt in culpa qui officia deserunt mollit anim id est laborum. Lorem ipsum dolor sit amet, consectetur adipiscing elit, sed do eiusmod tempor incididunt ut labore et dolore magna aliqua. Ut enim ad minim veniam, quis nostrud exercitation ullamco laboris nisi ut aliquip ex ea commodo consequat.</p>

    <p class="about-text" style="top:970px;">Duis aute irure dolor in reprehenderit in voluptate velit esse cillum dolore eu fugiat nulla pariatur. Excepteur sint occaecat cupidatat non proident, sunt in culpa qui officia deserunt mollit anim id est laborum.Lorem ipsum dolor sit amet, consectetur adipiscing elit, sed do eiusmod tempor incididunt ut labore et dolore magna aliqua. Ut enim ad minim veniam, quis nostrud exercitation ullamco laboris nisi ut aliquip ex ea commodo consequat. Duis aute irure dolor in reprehenderit in voluptate velit esse cillum dolore eu fugiat nulla pariatur. Excepteur sint occaecat cupidatat non proident, sunt in culpa qui officia deserunt mollit anim id est laborum.</p>
  </main>
</body>
</html>
```